Dunmore Roofing

Want a professional looking business card

Industry/Entity Type

Business

Contact Information for Business Card

Paul Dunmore ( Owner) paul@dunmoreroofing-example.com, www.dunmoreroofing-example.com, Adress: 4172 Township road 43 Ashcombe,ON K9X4T2

```html
<!DOCTYPE html>
<html lang="en">
<head>
<meta charset="utf-8">
<title>Dunmore Roofing – Business Card</title>
<link href="https://fonts.googleapis.com/css2?family=Roboto:wght@400;500&family=Roboto+Condensed:wght@500;700&display=swap" rel="stylesheet">
<style>
  :root {
    --brand-blue: #17407e;
    --brand-grey: #6d6e70;
    --rule-grey: #8a8a8a;
    --card-white: #f1f1f1;
    --text-dark: #3a3a3a;
    --backdrop: #262626;
    --on-blue: #ffffff;
  }
  html, body {
    margin: 0;
    width: 1200px;
    height: 960px;
    overflow: hidden;
    background: var(--backdrop);
  }
  .canvas {
    position: relative;
    width: 1200px;
    height: 960px;
  }
  .card {
    position: absolute;
    width: 600px;
    height: 342px;
    overflow: hidden;
  }
  /* Front */
  .card-front {
    left: 314px;
    top: 113px;
    background: var(--card-white);
    font-family: "Roboto", sans-serif;
  }
  .brand-lockup {
    position: absolute;
    right: 28px;
    top: 72px;
    display: flex;
    align-items: center;
    gap: 10px;
  }
  .brand-mark {
    width: 16px;
    height: 16px;
    background: var(--brand-blue);
  }
  .brand-name {
    font-family: "Roboto Condensed", sans-serif;
    font-weight: 700;
    font-size: 32px;
    letter-spacing: 1px;
    color: var(--brand-blue);
    line-height: 1;
  }
  .person-name {
    position: absolute;
    left: 25px;
    top: 197px;
    margin: 0;
    font-family: "Roboto Condensed", sans-serif;
    font-weight: 500;
    font-size: 24px;
    color: var(--brand-blue);
    line-height: 1;
  }
  .person-role {
    position: absolute;
    left: 25px;
    top: 224px;
    width: 547px;
    display: flex;
    align-items: center;
    gap: 3px;
    font-size: 15px;
    color: var(--brand-grey);
  }
  .person-role::after {
    content: "";
    flex: 1;
    height: 1px;
    background: var(--rule-grey);
  }
  .contact-list {
    position: absolute;
    left: 25px;
    top: 253px;
    margin: 0;
    padding: 0;
    list-style: none;
    font-size: 14.5px;
    color: var(--text-dark);
  }
  .contact-list li {
    display: flex;
    align-items: center;
    gap: 8px;
    height: 19px;
  }
  .contact-list svg { width: 13px; height: 13px; fill: var(--brand-blue); }
  .address {
    position: absolute;
    right: 28px;
    top: 254px;
    margin: 0;
    font-style: normal;
    text-align: right;
    font-size: 14.5px;
    line-height: 19px;
    color: var(--text-dark);
  }
  .footer-bands {
    position: absolute;
    left: 0;
    bottom: 0;
    width: 600px;
    height: 34px;
  }
  .website-front {
    position: absolute;
    right: 16px;
    bottom: 10px;
    font-size: 12.5px;
    letter-spacing: 0.6px;
    color: var(--on-blue);
  }
  /* Back */
  .card-back {
    left: 311px;
    top: 472px;
    background: var(--brand-blue);
    font-family: "Roboto", sans-serif;
    color: var(--on-blue);
  }
  .back-lockup {
    position: absolute;
    left: 0;
    right: 0;
    top: 138px;
    display: flex;
    justify-content: center;
    align-items: center;
    gap: 14px;
  }
  .back-lockup .brand-mark { width: 22px; height: 22px; background: var(--on-blue); }
  .back-lockup .brand-name { color: var(--on-blue); font-size: 48px; }
  .website-back {
    position: absolute;
    left: 0;
    right: 0;
    top: 286px;
    text-align: center;
    font-size: 14px;
    letter-spacing: 4.5px;
  }
</style>
</head>
<body>
<main class="canvas">
  <section class="card card-front" aria-label="Business card front">
    <div class="brand-lockup">
      <span class="brand-mark"></span>
      <span class="brand-name">DUNMORE ROOFING</span>
    </div>

    <h1 class="person-name">PAUL DUNMORE</h1>
    <div class="person-role">OWNER</div>

    <ul class="contact-list">
      <li>
        <svg viewBox="0 0 24 24" aria-hidden="true"><path d="M6.6 10.8c1.4 2.8 3.8 5.1 6.6 6.6l2.2-2.2c.3-.3.7-.4 1-.2 1.1.4 2.3.6 3.6.6.6 0 1 .4 1 1V20c0 .6-.4 1-1 1C10.6 21 3 13.4 3 4c0-.6.4-1 1-1h3.5c.6 0 1 .4 1 1 0 1.3.2 2.5.6 3.6.1.3 0 .7-.2 1L6.6 10.8z"/></svg>
        <span>613 555 0147</span>
      </li>
      <li>
        <svg viewBox="0 0 24 24" aria-hidden="true"><path d="M2 5h20v14H2z" fill="var(--brand-blue)"/><path d="M3 6l9 6.3L21 6" fill="none" stroke="#fff" stroke-width="1.6"/></svg>
        <span>paul@dunmoreroofing-example.com</span>
      </li>
    </ul>

    <address class="address">4172 Township road 43<br>Ashcombe, ON K9X4T2</address>

    <svg class="footer-bands" viewBox="0 0 600 34" aria-hidden="true">
      <polygon points="0,19 332,19 323,34 0,34" fill="var(--brand-grey)"/>
      <polygon points="348,0 600,0 600,34 327,34" fill="var(--brand-blue)"/>
    </svg>
    <span class="website-front">www.dunmoreroofing-example.com</span>
  </section>

  <section class="card card-back" aria-label="Business card back">
    <div class="back-lockup">
      <span class="brand-mark"></span>
      <span class="brand-name">DUNMORE ROOFING</span>
    </div>
    <div class="website-back">www.dunmoreroofing-example.com</div>
  </section>
</main>
</body>
</html>
```